Redesign This Psychology Website

We would like a slight redesign of this successful psychology (relationship counselling) website:

www.TheKelvaleClinic.com.au

We are updating the website, and we'd like a slight refresh of the design and style.

Please keep to very similar colours, and use the same logo. We're looking for around 10 page templates, however the main one is the home page.

Keep in mind, this website already converts quite well, so we want a new, fresh design in keeping with this one. Please don't bother designing something too extremely different.

thanks :)

Target Market(s)

couples who are looking for relationship counselling. Men and women, 25 - 70, across Australia

Industry/Entity Type

Psychology

Number of Pages Required

5+ page

Font styles to use
Sans Serif

Colors
87cfc6
b7a5cd
ec1f27
ffffff
cee9f5

Requirements
Must have
• a similar look to the current design, just looking for a slight refresh.
• Search bar
• Areas for lots of photos
• same logo
• lots of content areas
Nice to have
• great content areas, where we can display a lot of content and our areas.
Should not have
• no colors like orange, etc.
• should not have a totally different feel.

```html
<!DOCTYPE html>
<html lang="en">
<head>
<meta charset="utf-8">
<title>The Kelvale Clinic – Our Blogs</title>
<link href="https://fonts.googleapis.com/css2?family=Open+Sans:wght@400;600;700&display=swap" rel="stylesheet">
<style>
:root{
  --teal:#87cfc6;
  --teal-deep:#5fb8b0;
  --link:#1f8fa0;
  --purple:#b7a5cd;
  --red:#ec1f27;
  --sky:#cee9f5;
  --white:#ffffff;
  --ink:#333333;
  --muted:#8a8a8a;
  --line:#dddddd;
  --panel:#f3f3f3;
}
*{box-sizing:border-box;margin:0;padding:0}
html,body{width:1200px;height:4176px;overflow:hidden}
body{position:relative;background:var(--white);font-family:"Open Sans",Arial,sans-serif;color:var(--ink)}
a{color:inherit;text-decoration:none}
.abs{position:absolute}

/* top bar */
.topbar{left:0;top:0;width:1200px;height:47px;background:#f0f0f0;border-bottom:1px solid var(--line)}
.topbar .join{position:absolute;left:148px;top:14px;font-size:13px;color:#666}
.topbar .util{position:absolute;right:128px;top:0;display:flex;height:47px;align-items:center}
.topbar .util a{font-size:13px;color:#666;padding:0 14px;border-left:1px solid var(--line);line-height:20px}
.topbar .util a:first-child{border-left:0}

/* header */
.brand{left:128px;top:74px;display:flex;align-items:center;gap:12px}
.brand .dot{width:46px;height:46px;border-radius:50%;background:var(--red)}
.brand .name{font-size:30px;font-weight:600;color:var(--link);line-height:1}
.search{left:473px;top:86px;width:354px;height:40px;border:1px solid #cccccc;border-radius:3px;display:flex;align-items:center;padding-left:12px;gap:10px;font-size:13px;color:#999}
.callus{right:134px;top:74px;text-align:right}
.callus .lbl{font-size:17px;color:var(--teal-deep)}
.callus .num{display:flex;align-items:center;gap:8px;font-size:24px;font-weight:600;color:var(--link)}

/* nav */
.mainnav{left:0;top:161px;width:1200px;height:70px;background:linear-gradient(#9bd8d0,var(--teal))}
.mainnav ul{list-style:none;display:flex;position:absolute;left:128px;width:944px;height:70px}
.mainnav li{flex:1 1 auto;display:flex;align-items:center;justify-content:center;text-align:center;color:var(--white);font-size:15px;font-weight:600;text-transform:uppercase;line-height:19px;border-left:1px solid rgba(255,255,255,.45);padding:0 10px}
.mainnav li:first-child{border-left:0}

/* hero */
.hero{left:0;top:231px;width:1200px;height:326px;background:linear-gradient(100deg,#8a6a52 0%,#c9a686 35%,#e8cfb4 60%,#b98363 100%)}
.hero h1{position:absolute;left:128px;top:170px;font-size:36px;font-weight:600;color:var(--white);letter-spacing:1px}

/* section headings */
.section-title{font-size:28px;font-weight:400;color:var(--ink)}

/* blog cards */
.post{width:304px}
.photo{display:block;width:100%;border-radius:1px}
.post .photo{height:139px}
.post h3{margin-top:12px;font-size:16px;font-weight:600;color:var(--link);line-height:21px}
.excerpt{margin-top:8px;font-size:13px;color:var(--muted);line-height:21px}
.more{display:inline-block;margin-top:8px;font-size:13px;font-weight:600;color:var(--red)}

.tone-a{background:linear-gradient(135deg,#b9a08a,#e6d3c0)}
.tone-b{background:linear-gradient(135deg,#f0a24a,#f7d98c 60%,#3a2a1a)}
.tone-c{background:linear-gradient(135deg,#9c7b65,#e3c9b2)}
.tone-d{background:linear-gradient(135deg,#6e7fa0,#c8b8a8)}
.tone-e{background:linear-gradient(135deg,#d8b99a,#f1e4d6)}
.tone-f{background:linear-gradient(135deg,#9fd0d8,#e9dccd)}
.tone-g{background:linear-gradient(135deg,#3a2a24,#9a6c52)}
.tone-h{background:linear-gradient(135deg,#7cb3c9,#d7c3ad)}
.tone-i{background:linear-gradient(135deg,#c7c7c7,#f0eeec)}

/* sidebar */
.finder{left:768px;top:599px;width:298px;height:361px;background:var(--purple);padding:24px 22px}
.finder h2{text-align:center;color:var(--white);font-size:21px;font-weight:600;line-height:28px}
.finder label{display:block;margin-top:14px;font-size:13px;color:var(--white)}
.field{margin-top:6px;height:32px;background:var(--white);border-radius:2px;font-size:12px;color:#999;display:flex;align-items:center;justify-content:space-between;padding:0 10px}
.finder .btn{margin-top:20px;height:38px;background:var(--red);color:var(--white);font-size:15px;font-weight:600;display:flex;align-items:center;justify-content:center}

.cats{left:768px;top:988px;width:298px;height:872px;border:1px solid var(--line)}
.cats h2{height:48px;background:var(--purple);color:var(--white);font-size:18px;font-weight:600;line-height:48px;padding-left:28px}
.cats ul{list-style:none;padding:14px 0 0 24px}
.cats li{height:32px;font-size:13px;color:#555;display:flex;align-items:center;gap:10px}
.cats li::before{content:"";width:5px;height:5px;border-right:1.5px solid #888;border-top:1.5px solid #888;transform:rotate(45deg)}

.minis{left:768px;top:1901px;width:298px;display:flex;flex-direction:column;gap:14px}
.mini{height:114px;border:1px solid var(--line);display:flex}
.mini .photo{width:150px;height:112px}
.mini .body{padding:14px 0 0 14px;width:146px}
.mini h4{font-size:13px;font-weight:400;color:var(--ink);line-height:17px}
.mini .more{margin-top:4px;font-size:11px;color:var(--teal-deep)}

/* sex help */
.tabs{left:128px;top:2634px;width:618px;display:flex;gap:28px;border-bottom:1px solid var(--line);height:40px}
.tabs span{font-size:16px;color:var(--ink);padding-top:8px}
.tabs .on{color:var(--purple);border-bottom:3px solid var(--purple)}
.item{left:128px;width:618px;display:flex;gap:22px}
.item .photo{width:192px;height:134px;flex:none}
.item h3{font-size:16px;font-weight:600;color:var(--link);line-height:22px}
.item .excerpt{margin-top:10px}

.chev{left:582px;top:3722px}

/* footer */
.footer{left:0;top:3800px;width:1200px;height:293px;background:#fafafa;border-top:1px solid #e6e6e6;box-shadow:inset 0 10px 16px -12px rgba(0,0,0,.18)}
.footer .brand{top:78px}
.fcol{top:74px}
.fcol h5{font-size:15px;font-weight:700;color:var(--link);letter-spacing:.5px;margin-bottom:10px}
.fcol p{font-size:13px;color:#555;line-height:22px}
.social{display:flex;gap:8px;margin-top:10px}
.social i{width:30px;height:30px;border-radius:50%;display:block;background:var(--teal-deep)}
.legal{left:0;top:4093px;width:1200px;height:83px;background:#eeeeee;text-align:center;line-height:83px;font-size:12px;color:#888}
</style>
</head>
<body>

<header>
  <div class="abs topbar">
    <a class="join" href="#">Join Our Associate Program →</a>
    <nav class="util"><a href="#">Home</a><a href="#">Cart</a><a href="#">Blog</a><a href="#">Resources</a><a href="#">Contact</a></nav>
  </div>

  <a class="abs brand" href="#">
    <span class="dot"></span>
    <span class="name">The Kelvale Clinic</span>
  </a>

  <div class="abs search">
    <svg width="14" height="14" viewBox="0 0 14 14"><circle cx="6" cy="6" r="4.5" fill="none" stroke="#999" stroke-width="1.5"/><line x1="9.3" y1="9.3" x2="13" y2="13" stroke="#999" stroke-width="1.5"/></svg>
    Search here
  </div>

  <div class="abs callus">
    <div class="lbl">Call Us Now</div>
    <div class="num">
      <svg width="22" height="22" viewBox="0 0 24 24"><path d="M6.6 10.8a15 15 0 0 0 6.6 6.6l2.2-2.2c.3-.3.7-.4 1-.2 1.1.4 2.3.6 3.6.6.6 0 1 .4 1 1V20c0 .6-.4 1-1 1A17 17 0 0 1 3 4c0-.6.4-1 1-1h3.5c.6 0 1 .4 1 1 0 1.3.2 2.5.6 3.6.1.3 0 .7-.2 1z" fill="var(--red)"/></svg>
      1300 555 019
    </div>
  </div>

  <nav class="abs mainnav">
    <ul>
      <li>Counselling<br>Types</li>
      <li>Relationship Counselling<br>Locations</li>
      <li>Sex Therapy<br>Locations</li>
      <li>About Us</li>
      <li>Quizzes</li>
      <li>FAQ's</li>
      <li>Contact</li>
    </ul>
  </nav>
</header>

<section class="abs hero" role="img" aria-label="Photo of a smiling couple making a heart shape with their hands">
  <h1>OUR BLOGS</h1>
</section>

<main>
  <h2 class="abs section-title" style="left:128px;top:606px">Relationship Help and Advice</h2>

  <article class="abs post" style="left:128px;top:660px">
    <div class="photo tone-a" role="img" aria-label="Photo of a couple embracing"></div>
    <h3>Ending Your Relationship With Respect and Even a Little Kindness</h3>
    <p class="excerpt">Ending Your Relationship With Respect and Even a Little Kindness</p>
    <a class="more" href="#">Read More</a>
  </article>
  <article class="abs post" style="left:445px;top:660px">
    <div class="photo tone-b" role="img" aria-label="Photo of a couple silhouetted at sunset"></div>
    <h3>Is one of you an Intimacy Withholder?</h3>
    <p class="excerpt">Do you feel like strangers? or just flat mates? One of the most important aspects of a marriage and a...</p>
    <a class="more" href="#">Read More</a>
  </article>

  <article class="abs post" style="left:128px;top:966px">
    <div class="photo tone-c" role="img" aria-label="Photo of a happy couple"></div>
    <h3>Keys to being Psychologically Healthy (and therefore having healthy relationships)</h3>
    <p class="excerpt">Ending Your Relationship With Respect and Even a Little Kindness</p>
    <a class="more" href="#">Read More</a>
  </article>
  <article class="abs post" style="left:445px;top:966px">
    <div class="photo tone-d" role="img" aria-label="Photo of a couple walking hand in hand"></div>
    <h3>Would You Know If You're In An Emotionally Abusive Relationship?</h3>
    <p class="excerpt">Ending Your Relationship With Respect and Even a Little Kindness</p>
    <a class="more" href="#">Read More</a>
  </article>

  <article class="abs post" style="left:128px;top:1292px">
    <div class="photo tone-e" role="img" aria-label="Photo of a couple holding hands"></div>
    <h3>Have you lost yourself in your relationship?</h3>
    <p class="excerpt">Ending Your Relationship With Respect and Even a Little Kindness</p>
    <a class="more" href="#">Read More</a>
  </article>
  <article class="abs post" style="left:445px;top:1292px">
    <div class="photo tone-f" role="img" aria-label="Photo of a couple relaxing outdoors"></div>
    <h3>How do I contribute to our relationship problem?</h3>
    <p class="excerpt">Your Enneagram Profile If you really want to look in depth at why the two of you have the</p>
    <a class="more" href="#">Read More</a>
  </article>

  <article class="abs post" style="left:128px;top:1595px">
    <div class="photo tone-c" role="img" aria-label="Photo of a smiling couple"></div>
    <h3>Keys to being Psychologically Healthy (and therefore having healthy relationships)</h3>
    <p class="excerpt">Ending Your Relationship With Respect and Even a Little Kindness</p>
    <a class="more" href="#">Read More</a>
  </article>
  <article class="abs post" style="left:445px;top:1595px">
    <div class="photo tone-g" role="img" aria-label="Photo of a couple close together"></div>
    <h3>Why relationships go wrong</h3>
    <p class="excerpt">Relationships can be the most rewarding and most frustrating areas of our lives. Very few of us have been...</p>
    <a class="more" href="#">Read More</a>
  </article>

  <article class="abs post" style="left:128px;top:1915px">
    <div class="photo tone-a" role="img" aria-label="Photo of a happy couple"></div>
    <h3>Keys to being Psychologically Healthy (and therefore having healthy relationships)</h3>
    <p class="excerpt">Ending Your Relationship With Respect and Even a Little Kindness</p>
    <a class="more" href="#">Read More</a>
  </article>
  <article class="abs post" style="left:445px;top:1915px">
    <div class="photo tone-i" role="img" aria-label="Photo of a couple in conversation"></div>
    <h3>Would You Know If You're In An Emotionally Abusive Relationship?</h3>
    <p class="excerpt">Ending Your Relationship With Respect and Even a Little Kindness</p>
    <a class="more" href="#">Read More</a>
  </article>

  <article class="abs post" style="left:128px;top:2241px">
    <div class="photo tone-h" role="img" aria-label="Photo of a couple at the beach"></div>
    <h3>Have you lost yourself in your relationship?</h3>
    <p class="excerpt">Ending Your Relationship With Respect and Even a Little Kindness</p>
    <a class="more" href="#">Read More</a>
  </article>
  <article class="abs post" style="left:445px;top:2241px">
    <div class="photo tone-g" role="img" aria-label="Photo of a couple embracing"></div>
    <h3>How do I contribute to our relationship problem?</h3>
    <p class="excerpt">Your Enneagram Profile If you really want to look in depth at why the two of you have the</p>
    <a class="more" href="#">Read More</a>
  </article>

  <h2 class="abs section-title" style="left:128px;top:2570px">Sex Help and Advice</h2>
  <div class="abs tabs"><span class="on">FOR WOMEN</span><span>FOR MEN</span><span>FOR COUPLE</span></div>

  <article class="abs item" style="top:2706px">
    <div class="photo tone-e" role="img" aria-label="Photo of a thoughtful woman"></div>
    <div><h3>Difficulty Orgasming: How can I<br>experience more pleasure?</h3>
    <p class="excerpt">Is Your Orgasm Hard Work or Impossible? About 10% of women are non-orgasmic. It is between 5 to 10 times harder...</p>
    <a class="more" href="#">Read More</a></div>
  </article>
  <article class="abs item" style="top:2884px">
    <div class="photo tone-c" role="img" aria-label="Photo of a couple lying together"></div>
    <div><h3>Low libido in women: Why have I lost<br>my desire?</h3>
    <p class="excerpt">Generally women have far more blocks to sexual fulfilment than men. That's not really surprising when you think of...</p>
    <a class="more" href="#">Read More</a></div>
  </article>
  <article class="abs item" style="top:3048px">
    <div class="photo tone-a" role="img" aria-label="Photo of a couple sharing a tender moment"></div>
    <div><h3>Sensual touch: the cornerstone of a<br>great sex life.</h3>
    <p class="excerpt">Do you lovingly touch your partner, children, friends or family? Often? Ever wondered why people who recoil from touch</p>
    <a class="more" href="#">Read More</a></div>
  </article>
  <article class="abs item" style="top:3215px">
    <div class="photo tone-g" role="img" aria-label="Photo of a couple in an intimate embrace"></div>
    <div><h3>Tantra vs Porn – Learning How To Be<br>Intimate</h3>
    <p class="excerpt">What if studying tantra could heal our addiction to Porn? What if tapping into our natural abilities to experience...</p>
    <a class="more" href="#">Read More</a></div>
  </article>
  <article class="abs item" style="top:3383px">
    <div class="photo tone-d" role="img" aria-label="Photo of a couple relaxing together"></div>
    <div><h3>Maintaining desire: Keeping sex exciting in a long<br>term relationship.</h3>
    <p class="excerpt">What if studying tantra could heal our addiction to Porn? What if tapping into our natural abilities to experience...</p>
    <a class="more" href="#">Read More</a></div>
  </article>
  <article class="abs item" style="top:3558px">
    <div class="photo tone-g" role="img" aria-label="Photo of a couple in a close moment"></div>
    <div><h3>Differing libidos: How to manage<br>them in a healthy way.</h3>
    <p class="excerpt">Do you lovingly touch your partner, children, friends or family? Often? Ever wondered why people who recoil from touch</p>
    <a class="more" href="#">Read More</a></div>
  </article>

  <svg class="abs chev" width="36" height="20" viewBox="0 0 36 20"><polyline points="2,2 18,17 34,2" fill="none" stroke="#bbbbbb" stroke-width="3"/></svg>
</main>

<aside>
  <form class="abs finder">
    <h2>Find Our Psychologist<br>Near You</h2>
    <label>Type of Counselling</label>
    <div class="field">Select <svg width="10" height="6" viewBox="0 0 10 6"><polyline points="1,1 5,5 9,1" fill="none" stroke="#666" stroke-width="1.5"/></svg></div>
    <label>Location</label>
    <div class="field"></div>
    <label>Postcode</label>
    <div class="field"></div>
    <div class="btn">SEARCH</div>
  </form>

  <nav class="abs cats">
    <h2>Blogs Categories</h2>
    <ul>
      <li>Affairs</li><li>Assertiveness</li><li>Attachment</li><li>Break up</li><li>Communication</li>
      <li>Compatibility</li><li>Controlling</li><li>Couples counselling</li><li>Empathy</li><li>Enneagram</li>
      <li>Financial stress</li><li>Individual counselling for relationships</li><li>Infertility</li><li>Intimacy</li><li>Marriage counselling</li>
      <li>Narcissism</li><li>Personal growth</li><li>Personality</li><li>psychological wellbeing</li><li>Psychologist Interviews</li>
      <li>Relationship counselling</li><li>Relationship happiness</li><li>Relationship problems</li><li>Singles</li><li>Uncategorized</li>
    </ul>
  </nav>

  <div class="abs minis">
    <article class="mini"><div class="photo tone-e" role="img" aria-label="Photo of a couple holding hands"></div><div class="body"><h4>What can I do if I'm living with a Narcissist?</h4><a class="more" href="#">Read More</a></div></article>
    <article class="mini"><div class="photo tone-g" role="img" aria-label="Photo of a worried woman"></div><div class="body"><h4>Are You Living With a Steamroller?</h4><a class="more" href="#">Read More</a></div></article>
    <article class="mini"><div class="photo tone-c" role="img" aria-label="Photo of a couple talking"></div><div class="body"><h4>Did Your Relationship Start on Rocky Ground?</h4><a class="more" href="#">Read More</a></div></article>
    <article class="mini"><div class="photo tone-a" role="img" aria-label="Photo of a woman looking away"></div><div class="body"><h4>Why am I with a Narcissist?</h4><a class="more" href="#">Read More</a></div></article>
    <article class="mini"><div class="photo tone-i" role="img" aria-label="Photo of a couple sitting apart"></div><div class="body"><h4>Letter for a Partner Doubtful About Relationship Counselling</h4><a class="more" href="#">Read More</a></div></article>
    <article class="mini"><div class="photo tone-f" role="img" aria-label="Photo of a couple outdoors"></div><div class="body"><h4>What Are You Like In a Relationship?</h4><a class="more" href="#">Read More</a></div></article>
    <article class="mini"><div class="photo tone-g" role="img" aria-label="Photo of a couple in a tense moment"></div><div class="body"><h4>How Do I Know If I'm With A Narcissist?</h4><a class="more" href="#">Read More</a></div></article>
    <article class="mini"><div class="photo tone-c" role="img" aria-label="Photo of a couple embracing"></div><div class="body"><h4>Do You Wonder Why You and Your Partner Are Together?</h4><a class="more" href="#">Read More</a></div></article>
    <article class="mini"><div class="photo tone-d" role="img" aria-label="Photo of a couple at work"></div><div class="body"><h4>Is Your Pursuit of Success Sabotaging Your Relationships That Matter Most?</h4><a class="more" href="#">Read More</a></div></article>
    <article class="mini"><div class="photo tone-i" role="img" aria-label="Photo of a couple in conversation"></div><div class="body"><h4>How Do I Know If I'm With A Narcissist?</h4><a class="more" href="#">Read More</a></div></article>
    <article class="mini"><div class="photo tone-e" role="img" aria-label="Photo of a couple embracing"></div><div class="body"><h4>Do You Wonder Why You and Your Partner Are Together?</h4><a class="more" href="#">Read More</a></div></article>
    <article class="mini"><div class="photo tone-a" role="img" aria-label="Photo of a couple smiling"></div><div class="body"><h4>Is Your Pursuit of Success Sabotaging Your Relationships That Matter Most?</h4><a class="more" href="#">Read More</a></div></article>
  </div>
</aside>

<footer>
  <div class="abs footer">
    <a class="abs brand" href="#" style="left:140px">
      <span class="dot"></span>
      <span class="name">The Kelvale Clinic</span>
    </a>
    <div class="abs fcol" style="left:462px">
      <h5>QUICK LINKS</h5>
      <p>Home<br>About Us<br>Our Blogs<br>Shop Cart<br>Contact Us</p>
    </div>
    <div class="abs fcol" style="left:629px">
      <h5>RESOURCES</h5>
      <p>Counselling Type<br>Sex Therapy<br>Quizzes<br>FAQ<br>Relationship Counselling</p>
    </div>
    <div class="abs fcol" style="left:832px">
      <h5>CONTACT US</h5>
      <p>12 Example Street Suite 4<br>1300 555 019<br>Email: info@kelvaleclinic.com.au</p>
      <div class="social"><i></i><i></i><i></i><i></i></div>
    </div>
  </div>
  <div class="abs legal">© 2017 Company Name. All rights reserved.</div>
</footer>

</body>
</html>
```